Bold and colurful E-liquid Design Template

I'm looking for a new label for my house range of CLOUDHOUSE. I currently have almost 40 flavours, so I'm looking for a single label design that I can modify to create the rest of the flavours.
Each label will have the same design, but I'll change the color for each flavour and the name.
I'd like the label to be predominantly text based with bold text and bold colours. I like bold typographic styles. Also for each flavour I'd like to add 1 - 3 letters to represent the flavour. This can be in a larger font.
eg for
Blueberry I'll use the letter B
Pineapple Peach will use PP
Cinnamon Blueberry Muffin uses CBM
The colour used on the label will also be important so they stand out nicely on the shelf.
I've attached a psd mockup of the bottles I'll be using.

```html
<!DOCTYPE html>
<html lang="en">
<head>
<meta charset="utf-8">
<title>E-liquid Label Range</title>
<link href="https://fonts.googleapis.com/css2?family=Orbitron:wght@700&display=swap" rel="stylesheet">
<style>
  :root {
    --stage: #67686c;
    --label-black: #070707;
    --ink-white: #f4f4f4;
    --berry: #9c1d5c;
    --amber: #efa53a;
    --sky: #22a3de;
  }
  * { margin: 0; padding: 0; box-sizing: border-box; }
  html, body { width: 1098px; height: 1200px; overflow: hidden; }
  body {
    background: var(--stage);
    display: flex;
    justify-content: center;
    align-items: center;
    gap: 60px;
  }
  .label {
    width: 290px;
    height: 920px;
    background: var(--label-black);
    display: flex;
    flex-direction: column;
    align-items: center;
  }
  .label--berry { --accent: var(--berry); }
  .label--amber { --accent: var(--amber); }
  .label--sky   { --accent: var(--sky); }

  .flavour-band {
    width: 100%;
    height: 74px;
    margin-top: 18px;
    background: var(--accent);
    display: flex;
    align-items: center;
    justify-content: center;
  }
  .flavour-name, .volume, .strength, .house-name {
    font-family: "Orbitron", sans-serif;
    font-weight: 700;
    color: var(--ink-white);
    letter-spacing: 1px;
  }
  .flavour-name { font-size: 24px; }

  .house-name-area {
    flex: 1;
    width: 100%;
    display: flex;
    justify-content: center;
    align-items: center;
    padding: 24px 0;
  }
  .house-name {
    writing-mode: vertical-rl;
    transform: rotate(180deg);
    font-size: 58px;
    line-height: 1;
    letter-spacing: 4px;
    white-space: nowrap;
  }

  .volume-band {
    width: 86%;
    height: 62px;
    background: var(--accent);
    display: flex;
    align-items: center;
    justify-content: center;
  }
  .volume { font-size: 24px; }
  .strength {
    font-size: 22px;
    height: 120px;
    display: flex;
    align-items: center;
  }
</style>
</head>
<body>
  <section class="label label--berry">
    <div class="flavour-band"><span class="flavour-name">BLUEBERRY</span></div>
    <div class="house-name-area"><span class="house-name">CLOUDHOUSE</span></div>
    <div class="volume-band"><span class="volume">100ML</span></div>
    <div class="strength">3MG</div>
  </section>
  <section class="label label--amber">
    <div class="flavour-band"><span class="flavour-name">BLUEBERRY</span></div>
    <div class="house-name-area"><span class="house-name">CLOUDHOUSE</span></div>
    <div class="volume-band"><span class="volume">100ML</span></div>
    <div class="strength">3MG</div>
  </section>
  <section class="label label--sky">
    <div class="flavour-band"><span class="flavour-name">BLUEBERRY</span></div>
    <div class="house-name-area"><span class="house-name">CLOUDHOUSE</span></div>
    <div class="volume-band"><span class="volume">100ML</span></div>
    <div class="strength">3MG</div>
  </section>
</body>
</html>
```